Lotstallmart.com Webpage Design

Design Brief for lotstallmart.com (Copy of Brief also in attached Word file)

Name of Website- lotstallmart.com (existing logo and look & feel of website to be changed)

Logo - Finalised. The logo files are attached with the brief as “logo.jpeg”. The “Blue- Grey” version of the logo is for use on lighter backgrounds and the “Orange-White” version of the logo is for use on darker backgrounds. (A full Black version of the logo is also attached). Both versions may be used in different parts of the website. All attached files are in .png format.
Status - The website in functional and is undergoing user trials. However, we want to improve the look & feel of the website so at it seems
a. cotemporary,
b. Easy to Navigate
c. professional and
d. Vibrant.

Please visit ‘lotstallmart.com’ to check out the website and its functionalities – please use it only as a reference for the features & functions to be provided, however the designer should use a ‘Free Hand’ in designing the composition of various parts of the webpage without getting too influenced by the existing design

Objective of the Website ‘lotstallmart.com –
a. It is a portal focussed on listing of ‘Retail’ specific real-estate properties by developers, owners and realty brokers. The properties shall listed under the following four categories-
i. Retail Malls
ii. Shopping Complexes
iii. High-street shops
iv. Retail Warehouses
*refer lotstallmart.com for better clarity

b. The abovementioned properties shall be listed either for ‘Sale’ or ‘rent\lease’ or both

c. Users shall visit the site in case they wish to acquire a retail \ shop space either on ‘sale’ or ‘rent’. These Users would be able to specify the ‘Search Criteria’ through the tool-bars provided on the website – the ‘Search Criteria’ shall comprise of ‘Type of space category’, ‘City’, ‘Locality’, transaction type ie ‘Rent \ Sale’ and ‘Area Range’

d. The main revenue model for the website shall be listing fee ( or advertising charges ) payable by those listing their properties on the website.

Three Main Pages of Website (lotstallmart.com) that need to be designed -
a. Main Home Page (visit the web link - http://lotstallmart.com/ ) - The main home page has the “Search Toolbar” for specifying of Search Criteria by the User. It shall also have the following features & functions-
i. Main Advertising Banner
ii. Featured Projects
iii. New Launches
iv. Toolbar with buttons – ‘Advertise with Us’, ‘Listings Alert’, ‘Mart Wizards’, ‘Advertiser Login’

b. Property Listings Page (visit the web link - http://lotstallmart.com/gurgaon-in-india ) - The List of property options that match the Criteria specified by the ‘User’ get displayed on this page.

c. Property Detail Page - When the ‘User’ clicks on the “More….” Button on the ‘Property Listings Page’ (given in point b. above) the web page with the details of the property opens. (For Example – visit the web link - http://lotstallmart.com/vorne-Shopping-Complex-vorne-quadrion-gurgaon-636 )

Note:- Please refer to attached ‘Shopping’ related images the designer may use them on the website to provide a look & feel of retail if required – either separately or rotate in a single window

Target Market(s)

Retailers & Investors looking for retail space, Real Estate Brokers, Developers

Industry/Entity Type

Advertising

Number of Pages Required

3 page

Requirements
Must have
• Refer to existing site lotstallmart.com -- all the existing functionalities are a must have.
Nice to have
• The Designer may use the retail related images on the website if required for making it more vibrant. Refer attached images Shopping(1-6).jpg

```html
<!DOCTYPE html>
<html lang="en">
<head>
<meta charset="utf-8">
<title>Lotstallmart.com</title>
<link href="https://fonts.googleapis.com/css2?family=Open+Sans:wght@400;600;700&display=swap" rel="stylesheet">
<style>
:root{
  --blue:#1b8fd8;
  --blue-dark:#1576b5;
  --ink:#3a3a3a;
  --muted:#8a8a8a;
  --line:#d9d9d9;
  --nav:#e9e9e9;
  --panel:#f3f3f3;
  --footer:#2f2f2f;
  --white:#ffffff;
}
*{box-sizing:border-box;margin:0;padding:0}
html,body{width:710px;height:1200px;overflow:hidden;background:var(--white)}
body{font-family:"Open Sans",Arial,sans-serif;color:var(--ink)}
.page{width:710px;height:1200px;position:relative;overflow:hidden}

.site-header{height:57px;display:flex;align-items:center;justify-content:space-between;padding:0 28px}
.brand{display:flex;align-items:center;gap:8px;font-weight:700;font-size:19px;color:var(--blue)}
.brand-mark{width:16px;height:16px;border-radius:50%;background:var(--blue)}
.btn-login{background:var(--blue);color:var(--white);font-size:8px;font-weight:700;letter-spacing:.5px;padding:7px 12px;border-radius:2px}

.main-nav{height:28px;background:var(--nav);display:flex;padding-left:28px;font-size:9px}
.main-nav a{display:flex;align-items:center;padding:0 14px;color:var(--ink);text-decoration:none}
.main-nav a.active{background:var(--blue);color:var(--white)}

.hero{position:relative;height:305px}
.hero-photo{position:absolute;inset:0;background:linear-gradient(115deg,#b8b3ac 0%,#d9d4cc 35%,#c9b59e 60%,#8e7f73 100%)}
.search-box{position:absolute;left:78px;top:196px;width:554px}
.search-tabs{display:flex;background:var(--blue)}
.search-tabs span{flex:1;display:flex;align-items:center;gap:6px;justify-content:center;height:30px;color:var(--white);font-size:9px;font-weight:600;border-right:1px solid rgba(255,255,255,.3)}
.search-tabs span:last-child{border-right:0}
.tab-icon{width:10px;height:10px;border:1.5px solid var(--white);border-radius:1px}
.search-form{background:rgba(255,255,255,.95);display:flex;gap:10px;align-items:flex-end;padding:8px 12px 10px}
.field{flex:1;font-size:7px;color:var(--muted)}
.field .select{margin-top:3px;height:16px;border:1px solid var(--line);background:var(--white);position:relative}
.field .select::after{content:"";position:absolute;right:5px;top:6px;border:3px solid transparent;border-top-color:var(--muted)}
.btn-search{background:var(--blue);color:var(--white);font-size:7px;font-weight:700;padding:5px 14px}

.section{padding:0 28px}
.section-title{font-size:15px;font-weight:400;color:var(--ink);margin:20px 0 10px}
.cards{display:flex;gap:18px}
.card{width:150px;text-align:center}
.card-photo{height:92px;position:relative}
.card-city{position:absolute;left:0;right:0;top:0;height:16px;background:var(--blue);color:var(--white);font-size:8px;font-weight:700;display:flex;align-items:center;justify-content:center;letter-spacing:.5px}
.card-name{font-size:10px;color:var(--blue);margin-top:7px}
.card-type{font-size:7.5px;color:var(--muted);margin-top:1px}
.btn-more{display:inline-block;margin-top:5px;border:1px solid var(--line);font-size:6.5px;padding:3px 10px;color:var(--ink)}

.info{position:absolute;left:0;top:830px;width:710px;height:300px;background:var(--panel);display:flex;gap:26px;padding:16px 28px}
.info-col{flex:1;font-size:7px;color:var(--muted);line-height:1.5}
.info-col h3{font-size:14px;font-weight:400;color:var(--ink);margin-bottom:10px}
.info-col p{margin-bottom:10px}
.label{color:var(--ink);margin-top:8px}
.input{height:16px;background:var(--white);border:1px solid var(--line);margin-top:3px;position:relative}
.input.select::after{content:"";position:absolute;right:5px;top:6px;border:3px solid transparent;border-top-color:var(--muted)}
.input.area{height:40px}
.btn-outline{display:inline-block;margin-top:12px;border:1px solid var(--line);background:var(--white);padding:4px 10px;font-size:6.5px;color:var(--ink)}

.site-footer{position:absolute;left:0;top:1130px;width:710px;height:70px;background:var(--footer);display:flex;flex-direction:column;align-items:center;justify-content:center;gap:8px}
.social{display:flex;gap:6px}
.social span{width:16px;height:16px;border-radius:50%;background:#bdbdbd}
.copyright{font-size:7px;color:#bdbdbd}
</style>
</head>
<body>
<div class="page">
  <header class="site-header">
    <div class="brand"><span class="brand-mark"></span>Lotstallmart.com</div>
    <div class="btn-login">ADVERTISER LOGIN</div>
  </header>
  <nav class="main-nav">
    <a class="active">Home</a><a>Advertise with us</a><a>Mart Wizards</a><a>Listing Alert</a><a>Contact</a>
  </nav>

  <section class="hero">
    <div class="hero-photo" role="img" aria-label="Shopper with bags in a bright shopping mall"></div>
    <div class="search-box">
      <div class="search-tabs">
        <span><i class="tab-icon"></i>Retail Malls</span>
        <span><i class="tab-icon"></i>Shopping Complex</span>
        <span><i class="tab-icon"></i>High Street Shops</span>
        <span><i class="tab-icon"></i>Retail ware houses</span>
      </div>
      <div class="search-form">
        <div class="field">Sale or Rent or Both<div class="select"></div></div>
        <div class="field">City<div class="select"></div></div>
        <div class="field">Search<div class="select"></div></div>
        <div class="field">Search keyword<div class="select"></div></div>
        <div class="btn-search">SEARCH</div>
      </div>
    </div>
  </section>

  <section class="section">
    <h2 class="section-title">Retail Projects</h2>
    <div class="cards">
      <div class="card"><div class="card-photo" role="img" aria-label="Shopping complex exterior" style="background:linear-gradient(#8fb6d6,#6e8aa0)"><div class="card-city">SURAT</div></div><div class="card-name">Marigold Arcade</div><div class="card-type">Shopping Complex</div><span class="btn-more">VIEW MORE</span></div>
      <div class="card"><div class="card-photo" role="img" aria-label="High street retail building" style="background:linear-gradient(#a9c7e0,#7b8c96)"><div class="card-city">FARIDABAD</div></div><div class="card-name">Vista 81 High Street</div><div class="card-type">Shopping Complex</div><span class="btn-more">VIEW MORE</span></div>
      <div class="card"><div class="card-photo" role="img" aria-label="Mall building lit at dusk" style="background:linear-gradient(#4f6f9a,#b08a5e)"><div class="card-city">CHENNAI</div></div><div class="card-name">The Regal Mall</div><div class="card-type">Retail Malls</div><span class="btn-more">VIEW MORE</span></div>
      <div class="card"><div class="card-photo" role="img" aria-label="Large mall facade" style="background:linear-gradient(#9cb9d4,#8a7a6c)"><div class="card-city">NEW DELHI</div></div><div class="card-name">Harbor Mall-Lotus Garden</div><div class="card-type">Shopping Complex</div><span class="btn-more">VIEW MORE</span></div>
    </div>

    <h2 class="section-title">New Launches</h2>
    <div class="cards">
      <div class="card"><div class="card-photo" role="img" aria-label="Mall interior with shoppers" style="background:linear-gradient(#c7a98a,#7d6b5e)"><div class="card-city">BHOPAL</div></div><div class="card-name">The Grand Bazaar Place</div><div class="card-type">Retail Malls</div><span class="btn-more">VIEW MORE</span></div>
      <div class="card"><div class="card-photo" role="img" aria-label="Modern retail tower" style="background:linear-gradient(#9fc3e3,#6b7f91)"><div class="card-city">INDIA</div></div><div class="card-name">Crest One</div><div class="card-type">Retail Malls</div><span class="btn-more">VIEW MORE</span></div>
      <div class="card"><div class="card-photo" role="img" aria-label="Mall exterior at evening" style="background:linear-gradient(#3e5a85,#c59a62)"><div class="card-city">MYSORE</div></div><div class="card-name">Meadow Mall</div><div class="card-type">Retail Malls</div><span class="btn-more">VIEW MORE</span></div>
      <div class="card"><div class="card-photo" role="img" aria-label="Shop-cum-office buildings" style="background:linear-gradient(#b3cde4,#8c8680)"><div class="card-city">MOHALI</div></div><div class="card-name">Town Core - SCO in Sector</div><div class="card-type">Shopping Complex</div><span class="btn-more">VIEW MORE</span></div>
    </div>
  </section>

  <section class="info">
    <div class="info-col">
      <h3>Listing Alert</h3>
      <p>Post your retail space need with us and our team will send you suitable options.</p>
      <div class="label">Email</div><div class="input"></div>
      <div class="label">Retail Format of Interest</div><div class="input select"></div>
      <div class="label">City</div><div class="input select"></div>
      <span class="btn-outline">SUBSCRIBE</span>
    </div>
    <div class="info-col">
      <h3>Mart Wizards</h3>
      <p>Post your retail space need with us and our wizards will call you back.</p>
      <div class="label">Email</div><div class="input"></div>
      <div class="label">Mobile Number</div><div class="input"></div>
      <div class="label">Add Description of Requirement</div><div class="input area"></div>
      <span class="btn-outline">SUBSCRIBE</span>
    </div>
    <div class="info-col">
      <h3>Lotstallmart.com</h3>
      <p>Lotstallmart.com is a specialised web portal for retail spaces, helping buyers and tenants find malls, shopping complexes and high street shops across India.</p>
      <p>High street shops, malls and retail warehouses are listed here by owners, developers and brokers, making it easy to compare options and act quickly.</p>
      <span class="btn-outline">LEARN MORE</span>
    </div>
  </section>

  <footer class="site-footer">
    <div class="social"><span></span><span></span><span></span><span></span><span></span><span></span></div>
    <div class="copyright">© 2015 Lotstallmart.com | privacy policy</div>
  </footer>
</div>
</body>
</html>
```